Stationery Design Project

We need, stationary designs for a store of children and juvenile furniture.
we have the logo. also need tags for the furniture with enought space to include description and options , maybe a 4" x 6" tag.

Target Market(s)

Parents of childrens and teens

Industry/Entity Type

Store

```html
<!DOCTYPE html>
<html lang="en">
<head>
<meta charset="utf-8">
<title>Nest2Grow Stationery</title>
<link rel="stylesheet" href="https://fonts.googleapis.com/css2?family=Open+Sans:wght@400;600;700&display=swap">
<style>
  :root {
    --backdrop: #e4e4e4;
    --paper: #ffffff;
    --teal: #55c4d1;
    --teal-deep: #3fa9b5;
    --orange: #f07522;
    --ink: #6d6e70;
    --ink-soft: #8a8b8d;
    --cloud: #e6e6e6;
    --edge: #d2d2d2;
  }
  * { margin: 0; padding: 0; box-sizing: border-box; }
  html, body { width: 1200px; height: 900px; overflow: hidden; }
  body {
    position: relative;
    background: var(--backdrop);
    font-family: "Open Sans", sans-serif;
    color: var(--ink);
  }
  .sheet { position: absolute; background: var(--paper); }

  /* brand lockup */
  .brand { position: absolute; display: flex; align-items: center; gap: 8px; white-space: nowrap; }
  .brand-mark { display: block; background: var(--teal); }
  .brand-name { font-family: "Open Sans", sans-serif; font-weight: 600; color: var(--ink); letter-spacing: 0.5px; }

  .icon { display: inline-flex; align-items: center; justify-content: center; border-radius: 50%; flex: none; }
  .icon svg { display: block; }
  .icon--orange { background: var(--orange); }
  .icon--teal { background: var(--teal); }

  .contact { position: absolute; display: flex; align-items: center; gap: 7px; font-size: 9px; color: var(--ink); white-space: nowrap; }

  /* faint cloud decoration: soft haze standing in for the drawn clouds */
  .cloud-haze {
    position: absolute;
    background:
      radial-gradient(ellipse 32% 50% at 22% 45%, var(--cloud) 0%, rgba(230,230,230,0) 100%),
      radial-gradient(ellipse 30% 48% at 50% 62%, var(--cloud) 0%, rgba(230,230,230,0) 100%),
      radial-gradient(ellipse 30% 46% at 78% 58%, var(--cloud) 0%, rgba(230,230,230,0) 100%);
  }

  /* letterhead */
  .letterhead { left: 67px; top: 66px; width: 701px; height: 352px; border: 1px solid var(--edge); }
  .letterhead .brand { left: 38px; top: 80px; }
  .letterhead .brand-mark { width: 22px; height: 22px; }
  .letterhead .brand-name { font-size: 22px; }
  .letterhead .address { position: absolute; left: 542px; top: 60px; display: flex; gap: 7px; font-size: 8px; line-height: 10px; }
  .letterhead .cloud-haze { left: 460px; top: 246px; width: 220px; height: 90px; }

  /* envelope */
  .envelope { left: 74px; top: 431px; width: 702px; height: 425px; }
  .envelope-flap { position: absolute; left: 0; top: 0; }
  .envelope .contact { top: 394px; font-size: 8.5px; }

  /* business card front */
  .card { position: absolute; width: 332px; height: 192px; border-radius: 16px; }
  .card-front { left: 808px; top: 241px; background: var(--paper); }
  .card-front .brand { right: 16px; top: 46px; gap: 5px; }
  .card-front .brand-mark { width: 10px; height: 10px; }
  .card-front .brand-name { font-size: 13px; }
  .card-front .cloud-haze { left: 16px; top: 44px; width: 115px; height: 50px; }
  .holder-name { position: absolute; left: 17px; top: 100px; font-size: 16px; font-weight: 600; color: var(--orange); line-height: 20px; }
  .holder-role { position: absolute; left: 17px; top: 117px; font-size: 9px; color: var(--ink-soft); }
  .card-front .contact { font-size: 9.5px; }

  /* business card back */
  .card-back { left: 807px; top: 476px; width: 331px; height: 190px; background: var(--teal); }
  .card-back .brand { left: 50%; top: 66px; transform: translateX(-50%); }
  .card-back .brand-mark { width: 14px; height: 14px; background: #fff; }
  .card-back .brand-name { font-size: 20px; color: #fff; }
  .card-back .web { position: absolute; left: 0; right: 0; top: 134px; text-align: center; font-size: 10px; font-weight: 700; color: #fff; }
</style>
</head>
<body>

<svg width="0" height="0" style="position:absolute" aria-hidden="true">
  <defs>
    <symbol id="i-phone" viewBox="0 0 10 10"><path d="M2.2 1.2l1.4 1.6-.7 1a5 5 0 0 0 2.3 2.3l1-.7 1.6 1.4-.9 1.2C4.6 8 2 5.4 1 2.1z" fill="#fff"/></symbol>
    <symbol id="i-mail" viewBox="0 0 10 10"><rect x="1.5" y="2.8" width="7" height="4.6" rx=".4" fill="#fff"/><path d="M1.8 3.1L5 5.5l3.2-2.4" fill="none" stroke="var(--orange)" stroke-width=".6"/></symbol>
    <symbol id="i-pin" viewBox="0 0 10 10"><path d="M5 1.2a2.7 2.7 0 0 0-2.7 2.7C2.3 6 5 8.8 5 8.8S7.7 6 7.7 3.9A2.7 2.7 0 0 0 5 1.2z" fill="#fff"/><circle cx="5" cy="3.9" r="1" fill="var(--orange)"/></symbol>
    <symbol id="i-globe" viewBox="0 0 10 10"><circle cx="5" cy="5" r="3.3" fill="none" stroke="#fff" stroke-width=".9"/><path d="M1.8 5h6.4M5 1.7c-1.6 2-1.6 4.6 0 6.6M5 1.7c1.6 2 1.6 4.6 0 6.6" fill="none" stroke="#fff" stroke-width=".7"/></symbol>
  </defs>
</svg>

<!-- Letterhead -->
<section class="sheet letterhead">
  <div class="brand">
    <span class="brand-mark"></span>
    <span class="brand-name">Nest2Grow</span>
  </div>
  <div class="address">
    <span class="icon icon--orange" style="width:15px;height:15px"><svg width="10" height="10"><use href="#i-pin"/></svg></span>
    <span>Office #, Building Street, City<br>&nbsp;State XXXXX Country</span>
  </div>
  <div class="cloud-haze" role="img" aria-label="Faint grey outline clouds drifting in the corner"></div>
</section>

<!-- Envelope -->
<section class="sheet envelope">
  <svg class="envelope-flap" width="702" height="140" viewBox="0 0 702 140" aria-hidden="true">
    <defs>
      <linearGradient id="flap-shade" x1="0" y1="0" x2="0" y2="1">
        <stop offset="0" stop-color="var(--teal)"/>
        <stop offset=".55" stop-color="var(--teal)"/>
        <stop offset="1" stop-color="var(--teal-deep)"/>
      </linearGradient>
    </defs>
    <polygon points="6,0 696,0 680,90 648,94 648,130 53,130 53,94 22,90" fill="url(#flap-shade)"/>
  </svg>
  <span class="contact" style="left:176px"><span class="icon icon--orange" style="width:15px;height:15px"><svg width="10" height="10"><use href="#i-phone"/></svg></span>555 0100 2468</span>
  <span class="contact" style="left:278px"><span class="icon icon--orange" style="width:15px;height:15px"><svg width="10" height="10"><use href="#i-mail"/></svg></span>hello@nest2grow.com</span>
  <span class="contact" style="left:421px"><span class="icon icon--orange" style="width:15px;height:15px"><svg width="10" height="10"><use href="#i-globe"/></svg></span>www.nest2grow.com</span>
</section>

<!-- Business card, front -->
<section class="card card-front">
  <div class="brand">
    <span class="brand-mark"></span>
    <span class="brand-name">Nest2Grow</span>
  </div>
  <div class="cloud-haze" role="img" aria-label="Faint grey outline clouds"></div>
  <h2 class="holder-name">Marlo Venn</h2>
  <p class="holder-role">Business Manager</p>
  <span class="contact" style="left:17px;top:141px"><span class="icon icon--teal" style="width:14px;height:14px"><svg width="9" height="9"><use href="#i-phone"/></svg></span>555 010 2468</span>
  <span class="contact" style="left:104px;top:141px"><span class="icon icon--teal" style="width:14px;height:14px"><svg width="9" height="9"><use href="#i-mail"/></svg></span>marlo@nest2grow.com</span>
  <span class="contact" style="left:17px;top:163px"><span class="icon icon--teal" style="width:14px;height:14px"><svg width="9" height="9"><use href="#i-pin"/></svg></span>Street, City State XXXXX Country</span>
</section>

<!-- Business card, back -->
<section class="card card-back">
  <div class="brand">
    <span class="brand-mark"></span>
    <span class="brand-name">Nest2Grow</span>
  </div>
  <p class="web">www.nest2grow.com</p>
</section>

</body>
</html>
```